Hardcore nerd needs to stand out in a sea of dull Defence business cards

Wombarra Devices is a new Australian consulting engineering company that turns research and theory into practical systems. No evangelistic fluff, just mathematics and physics into electronic and optical circuits for consumer products, scientific research or Defence applications.

We already have a recognised logo (provided) which is often dark blue/black on a light background but we're open to other combinations. (Us engineers tend to have limited aesthetic imagination :)

Some of our recent products have included:
* Instrumentation for electrical testing,
* Radar jammers,
* GPS antenna design,
* Satellite tracking systems,
* High power lasers

We're open to both single and double-sided designs - happy to be convinced either way.

P.S. Another group is working on the web page, so - alas - our web site is currently of no use for images/ideas...

Target Market(s)

Engineering managers,
Scientists

Contact Information for Business Card

Dr Colin Harte
R&D Engineer

colin@wombarradevices.com.au
0427 563 710

PO Box XXX (to be confirmed)
Kelsby ACT 2917
Australia

Font styles to use
Serif
Sans Serif

Colors

Designer to choose colors to be used in the design.

Requirements
Must have
• My contact details!
• I've had many (great) "bold and plain" designs submitted already, so feel free to be artistically creative :)
• Happy to take advice re fonts/colours/printability etc.
Nice to have
• I'm not sure if "lists" are more at home on a CV than a business card, but representative services include:
• Applied electromagnetics
• RF and high speed electronics
• Signal and image processing
• Electro-optical and laser systems
• Concept-to-prototype design services
• If you're considering double sided cards, then often measuring/alignment grids/rulers feature on the back of similar cards.
• e.g. https://www.veltranoptics.example/newgrouppage9.cfm?objectgroup_id=4183
• https://www.veltranoptics.example/newgrouppage9.cfm?objectgroup_ID=4185
• ..or even a "Smith chart" (google will return lots)
• Generic images to represent a capability might work - googling images associated with keyword for each of these areas might help:
• - "passive radar", "phased array", "fdtd", "vircator"
• RF and high speed electronic design
• - "smith chart", "microstrip circuits", "dimensioned drawing", "electronic schematic"
• - "dft", "iir filter"
• - "optical cavity". "laser energy level diagram"
• Background/watermarked images outlines/wireframes/schematics would probably look OK.
Should not have
• If a list of projects/services is provided, it is important not to make the client feel that this is "all" the company can do. Engineering design is a creative discipline (like graphics :)
• Please, no stock "military" snaps like planes, missiles, etc!

```html
<!DOCTYPE html>
<html lang="en">
<head>
<meta charset="utf-8">
<title>Wombarra Devices – Business Card</title>
<link href="https://fonts.googleapis.com/css2?family=Lato:ital,wght@0,400;0,700;0,900;1,700&display=swap" rel="stylesheet">
<style>
  :root {
    --navy: #1f295c;
    --orange: #f07d1f;
    --white: #ffffff;
    --stage: #e9e7e3;
    --ink: #2a2f4a;
  }
  * { margin: 0; padding: 0; box-sizing: border-box; }
  html, body {
    width: 1200px; height: 1200px; overflow: hidden;
    background: var(--stage);
    font-family: "Lato", Arial, sans-serif;
  }
  .card {
    position: absolute;
    left: 266px;
    width: 668px; height: 390px;
    border-radius: 22px;
    box-shadow: 0 4px 12px rgba(0,0,0,0.18);
    overflow: hidden;
  }
  .card--front { top: 185px; background: var(--white); }
  .card--back  { top: 625px; background: var(--navy); }

  .brand { position: absolute; display: flex; align-items: center; gap: 14px; }
  .brand__dot { border-radius: 50%; flex: none; }
  .brand__name {
    font-weight: 900; text-transform: uppercase; line-height: 1.02;
    letter-spacing: 1.5px;
  }
  .card--front .brand { top: 36px; right: 28px; }
  .card--front .brand__dot { width: 100px; height: 100px; background: var(--navy); }
  .card--front .brand__name { color: var(--navy); font-size: 31px; }
  .card--back .brand { top: 32px; right: 28px; }
  .card--back .brand__dot { width: 116px; height: 116px; background: var(--orange); }
  .card--back .brand__name { color: var(--white); font-size: 36px; }

  .person { position: absolute; left: 28px; top: 155px; right: 0; }
  .person__name { color: var(--orange); font-weight: 700; font-size: 26px; line-height: 1.2; }
  .person__role-row { display: flex; align-items: flex-end; gap: 4px; }
  .person__role { color: var(--navy); font-weight: 700; font-style: italic; font-size: 18px; line-height: 1.2; white-space: nowrap; }
  .person__rule { flex: 1; height: 1px; background: var(--orange); margin-bottom: 3px; }

  .contact { position: absolute; left: 28px; top: 248px; list-style: none; }
  .contact li { display: flex; align-items: center; gap: 12px; color: var(--ink); font-size: 19.5px; line-height: 25px; }
  .contact svg { width: 18px; height: 18px; flex: none; }

  .address {
    position: absolute; right: 24px; top: 337px;
    color: var(--navy); font-weight: 700; font-size: 19.5px;
  }

  .capabilities { position: absolute; left: 28px; top: 245px; list-style: none; }
  .capabilities li {
    display: flex; align-items: center; gap: 10px;
    color: var(--white); font-size: 19.5px; line-height: 24px;
  }
  .capabilities li::before {
    content: ""; width: 12px; height: 12px; border-radius: 50%;
    background: var(--orange); flex: none;
  }
</style>
</head>
<body>
  <section class="card card--front">
    <div class="brand">
      <span class="brand__dot"></span>
      <span class="brand__name">Wombarra<br>Devices</span>
    </div>

    <div class="person">
      <h1 class="person__name">Dr Colin Harte</h1>
      <div class="person__role-row">
        <span class="person__role">R&amp;D Engineer</span>
        <span class="person__rule"></span>
      </div>
    </div>

    <ul class="contact">
      <li>
        <svg viewBox="0 0 24 24" aria-hidden="true"><path fill="#f07d1f" d="M6.6 10.8a15.1 15.1 0 0 0 6.6 6.6l2.2-2.2c.3-.3.7-.4 1-.2 1.1.4 2.3.6 3.6.6.6 0 1 .4 1 1V20c0 .6-.4 1-1 1A17 17 0 0 1 3 4c0-.6.4-1 1-1h3.5c.6 0 1 .4 1 1 0 1.3.2 2.5.6 3.6.1.3 0 .7-.2 1z"/></svg>
        0427 563 710
      </li>
      <li>
        <svg viewBox="0 0 24 24" aria-hidden="true"><g fill="none" stroke="#f07d1f" stroke-width="1.8" stroke-linejoin="round"><path d="M3 10l9-6 9 6v10H3z"/><path d="M3 10l9 6 9-6"/></g></svg>
        colin@wombarradevices.com.au
      </li>
    </ul>

    <p class="address">PO Box XXX, Kelsby ACT 2917, Australia</p>
  </section>

  <section class="card card--back">
    <div class="brand">
      <span class="brand__dot"></span>
      <span class="brand__name">Wombarra<br>Devices</span>
    </div>

    <ul class="capabilities">
      <li>Radar jammers,</li>
      <li>High power lasers</li>
      <li>GPS antenna design,</li>
      <li>Satellite tracking systems,</li>
      <li>Instrumentation for electrical testing,</li>
    </ul>
  </section>
</body>
</html>
```